Professional looking Roller Blind Discount Card that portrays quality at a value for money price!

We need a double sided business card designed as a discount card. Size 90mm wide x 55mm high.We would like it to look professional and portray quality at a value for money price point.I have uploaded a word document with a basic layout with the information we want included on each side of the card. Please put your own thought into the layout.

Contact Information for Business Card

As per word document attached.

```html
<!DOCTYPE html>
<html lang="en">
<head>
<meta charset="utf-8">
<title>Roller Blinds Discount Card</title>
<link rel="stylesheet" href="https://fonts.googleapis.com/css2?family=Poppins:wght@400;500;700&family=Oswald:wght@500;700&family=Dancing+Script:wght@600&display=swap">
<style>
  :root {
    --brand-blue: #29a8e0;
    --brand-blue-deep: #1a7fd0;
    --ink: #3a3a3a;
    --charcoal: #2b2b2b;
    --paper: #ffffff;
    --backdrop: #e9ecef;
  }
  * { box-sizing: border-box; margin: 0; padding: 0; }
  html, body { width: 1200px; height: 900px; overflow: hidden; }
  body {
    background: var(--backdrop);
    font-family: "Poppins", sans-serif;
    color: var(--ink);
    position: relative;
  }
  .card {
    position: absolute;
    left: 270px;
    width: 660px;
    height: 403px;
    background: var(--paper);
    box-shadow: 0 6px 18px rgba(0,0,0,.18);
    overflow: hidden;
  }
  .card--front { top: 30px; }
  .card--back { top: 467px; }

  /* Front */
  .front__band {
    position: absolute; left: 0; top: 0; width: 100%; height: 84px;
    background: var(--brand-blue);
  }
  .front__title {
    position: absolute; left: 0; top: 2px; width: 100%;
    text-align: center; color: var(--paper);
    font-weight: 700; font-size: 68px; letter-spacing: 1px; line-height: 84px;
  }
  .front__subtitle {
    position: absolute; left: 40px; right: 30px; top: 88px;
    text-align: center; font-size: 30px; font-weight: 500; color: var(--ink);
  }
  .front__photo {
    position: absolute; left: 40px; top: 136px; width: 470px; height: 170px;
    background: linear-gradient(100deg, #6e5a4e 0%, #7d6a5c 22%, #5f7a4a 40%, #8fae6e 62%, #c9d4c0 80%, #a89680 100%);
  }
  .front__call {
    position: absolute; left: 40px; top: 306px; width: 470px; height: 54px;
    background: var(--brand-blue);
    color: var(--paper); font-size: 24px; line-height: 54px; text-align: center;
    letter-spacing: .5px;
  }
  .front__call strong { font-weight: 700; font-size: 27px; }
  .front__bubble { position: absolute; left: 528px; top: 150px; width: 118px; height: 90px; }
  .front__bubble-text {
    position: absolute; left: 528px; top: 166px; width: 118px;
    font-family: "Dancing Script", cursive; font-weight: 600;
    color: var(--paper); font-size: 17px; line-height: 19px; text-align: center;
  }
  .front__brand {
    position: absolute; left: 520px; top: 320px; width: 136px;
    text-align: center; color: var(--brand-blue-deep);
    font-family: "Poppins", sans-serif; font-weight: 700; font-size: 17px; letter-spacing: .5px;
  }

  /* Back */
  .back__band {
    position: absolute; left: 0; top: 34px; width: 100%; height: 100px;
    background: var(--brand-blue);
  }
  .back__offer {
    position: absolute; left: 0; top: 34px; width: 100%;
    text-align: center; color: var(--paper);
    font-weight: 700; font-size: 84px; line-height: 100px; letter-spacing: 2px;
  }
  .back__lead {
    position: absolute; left: 0; top: 140px; width: 100%;
    text-align: center; font-size: 27px; line-height: 34px; color: var(--ink);
  }
  .back__lead .dot { color: var(--brand-blue); }
  .back__seals {
    position: absolute; left: 30px; top: 214px; width: 600px;
    display: flex; justify-content: space-between;
  }
  .seal { position: relative; width: 180px; height: 130px; }
  .seal svg { position: absolute; left: 0; top: 0; }
  .seal__word {
    position: absolute; left: 0; top: 26px; width: 180px; text-align: center;
    font-family: "Oswald", sans-serif; font-weight: 700; font-size: 46px; line-height: 48px;
    color: var(--brand-blue);
  }
  .seal__note {
    position: absolute; left: 0; top: 76px; width: 180px; text-align: center;
    font-family: "Oswald", sans-serif; font-weight: 500; font-size: 13px;
    color: var(--paper); letter-spacing: .3px;
  }
  .back__call {
    position: absolute; left: 0; top: 350px; width: 100%;
    text-align: center; font-size: 30px; color: var(--ink); letter-spacing: .5px;
  }
  .back__call strong { color: var(--brand-blue); font-weight: 700; }
</style>
</head>
<body>

<section class="card card--front">
  <div class="front__band"></div>
  <h1 class="front__title">ROLLER BLINDS</h1>
  <p class="front__subtitle">FREE in Home Meacure &amp; Quote</p>
  <div class="front__photo" role="img" aria-label="Photo of a sunny room with roller blinds over windows looking onto a garden"></div>
  <p class="front__call">CALL <strong>0400 123 456</strong> TODAY!</p>
  <svg class="front__bubble" viewBox="0 0 118 90" aria-hidden="true">
    <defs>
      <linearGradient id="bubbleFill" x1="0" y1="0" x2="0" y2="1">
        <stop offset="0" stop-color="#5cc0ef"/>
        <stop offset="1" stop-color="#1a7fd0"/>
      </linearGradient>
    </defs>
    <ellipse cx="62" cy="38" rx="55" ry="34" fill="url(#bubbleFill)"/>
    <path d="M22 58 L8 86 L42 68 Z" fill="#1a7fd0"/>
  </svg>
  <p class="front__bubble-text">Huge Selection<br>of Fabrics</p>
  <p class="front__brand">B&amp;K INTERIORS</p>
</section>

<section class="card card--back">
  <div class="back__band"></div>
  <h2 class="back__offer">25% OFF</h2>
  <p class="back__lead">Quality Custom Made Roller Blinds<br>Blockout <span class="dot">•</span> screen <span class="dot">•</span> LightFiltering</p>

  <div class="back__seals">
    <div class="seal">
      <svg width="180" height="130" viewBox="0 0 180 130" aria-hidden="true">
        <circle cx="90" cy="65" r="62" fill="#29a8e0"/>
        <rect x="4" y="24" width="172" height="72" fill="#2b2b2b"/>
      </svg>
      <span class="seal__word">FREE</span>
      <span class="seal__note">IN HOME MEASURE &amp; QUOTE</span>
    </div>
    <div class="seal">
      <svg width="180" height="130" viewBox="0 0 180 130" aria-hidden="true">
        <circle cx="90" cy="65" r="62" fill="#29a8e0"/>
        <rect x="4" y="24" width="172" height="72" fill="#2b2b2b"/>
      </svg>
      <span class="seal__word">BEST</span>
      <span class="seal__note">PRICE GUARANTEE</span>
    </div>
    <div class="seal">
      <svg width="180" height="130" viewBox="0 0 180 130" aria-hidden="true">
        <circle cx="90" cy="65" r="62" fill="#29a8e0"/>
        <rect x="4" y="24" width="172" height="72" fill="#2b2b2b"/>
      </svg>
      <span class="seal__word">FAMILY</span>
      <span class="seal__note">OWNED &amp; OPERATED</span>
    </div>
  </div>

  <p class="back__call">CALL <strong>0400 123 456</strong> TODAY!</p>
</section>

</body>
</html>
```